Counseling Practice Business Card

I need a professional looking business card incorporating my new logo that was just completed. Card needs to incorporate my name and title, description of my specialty, my address, my phone number, my fax number, my email and my website URL. I need to be able to choose design on/with different paper colors and textures.
I do not have a lot of business card ideas so I am open to anything but I want bold,sharp, clear card without additional designs other than my logo (see attached file info). I am open to different color backgrounds or paper colors including black. I do not like traditional brackets around area codes in phone number or dashes between numbers in phone number. Am open to other ways of presenting including periods between numbers as appropriate. I do not know enough to know what I like yet but I want card to coordinate and work together with my logo. My practice emphasizes natural mental health interventions so any use of color (with background paper color or the blue and green in my logo) that elicits nature is nice. In addition to black, any natural brown or wood looking background might be desirable also. Most of the offerings so far look very similar and boring.

Target Market(s)

Potential therapy clients and other professionals

Contact Information for Business Card

Card information:
Gerald M. Whitcombe, Ph.D.
Licensed Clinical Psychologist
Integrative Health Coach
4812 Marlowe Ridge Blvd SE
Suite 310
Duluth, GA 30096
(770) 415-2983 phone
(770) 581-4096 fax
drgeraldwhitcombe@quillmarsh.net
brightfernwellness.net

Font styles to use
Serif
Sans Serif
Other font styles liked:
• anything that you think looks crisp, clear and easily readable

Requirements
Must have
• Any color used should coordinate with my logo design (see attached files).
• Card should be printed horizontally so top and bottom are longest sides of rectangle.
• Background color or paper color should complement and highlight logo. Do not like a white background. black, grey, brown or any color my logo would blend well with.
Nice to have
• I would like designer to utilize color to highlight letters/name or phone-fax-web symbols.
• Bottom edge of card could be highlighted if appropriate to an idea.
Should not have
• I would NOT want the card to have a pure white background at all.
• No clear cards.
• Cards should be oriented with long sides on bottom and top, NOT sides. DO NOT LIKE THIS THIN TALL ORIENTATION.

```html
<!DOCTYPE html>
<html lang="en">
<head>
<meta charset="utf-8">
<title>Brightfern Wellness – Business Card</title>
<link rel="stylesheet" href="https://fonts.googleapis.com/css2?family=Roboto+Condensed:wght@400;700&family=Roboto:wght@400&display=swap">
<style>
  :root {
    --backdrop: #d9d3ca;
    --card-black: #141518;
    --header-green: #006633;
    --brand-green: #2f8a4a;
    --accent-blue: #3a7fc1;
    --text-white: #ffffff;
    --text-grey: #c9cacc;
  }
  * { margin: 0; padding: 0; box-sizing: border-box; }
  html, body {
    width: 1200px; height: 960px; overflow: hidden;
    background: var(--backdrop);
  }
  .stage { position: relative; width: 1200px; height: 960px; }
  .card {
    position: absolute;
    width: 600px; height: 343px;
    background: var(--card-black);
    overflow: hidden;
    box-shadow: 0 3px 8px rgba(0,0,0,0.35);
  }
  .card--front { left: 314px; top: 113px; }
  .card--back  { left: 312px; top: 472px; width: 598px; height: 342px; }

  .header-band { position: absolute; left: 0; top: 0; width: 600px; height: 343px; }

  .identity {
    position: absolute; top: 24px; left: 0; width: 100%;
    text-align: center; color: var(--text-white);
    font-family: "Roboto Condensed", sans-serif;
  }
  .identity__name { font-weight: 700; font-size: 20px; letter-spacing: 0.2px; text-transform: uppercase; }
  .identity__title { font-weight: 400; font-size: 14.5px; margin-top: 3px; }

  .brand-name {
    position: absolute; left: 0; width: 100%;
    text-align: center;
    font-family: "Roboto Condensed", sans-serif;
    font-weight: 700;
    color: var(--brand-green);
    line-height: 1;
  }
  .card--front .brand-name { top: 152px; font-size: 40px; }
  .card--back .brand-name { top: 145px; font-size: 50px; }

  .contact {
    position: absolute; top: 243px; left: 0; width: 100%;
    text-align: center;
    font-family: "Roboto Condensed", sans-serif;
    font-size: 13.5px; line-height: 20.5px;
    color: var(--text-grey);
  }
  .contact__label { color: var(--accent-blue); }
</style>
</head>
<body>
<main class="stage">
  <section class="card card--front">
    <svg class="header-band" viewBox="0 0 600 343" aria-hidden="true">
      <path d="M0 0 H600 V150 C470 70 160 70 0 215 Z" fill="var(--header-green)"/>
    </svg>
    <div class="identity">
      <p class="identity__name">Gerald M. Whitcombe, Ph.D.</p>
      <p class="identity__title">Licensed Clinical Psychologist | Integrative Health Coach</p>
    </div>
    <p class="brand-name">Brightfern Wellness</p>
    <div class="contact">
      <p>4812 Marlowe Ridge Blvd SE, Suite 310, Duluth, GA 30096</p>
      <p><span class="contact__label">P:</span> (770) 415-2983 <span class="contact__label">F:</span> (770) 581-4096 drgeraldwhitcombe@quillmarsh.net</p>
      <p>www.brightfernwellness.net</p>
    </div>
  </section>

  <section class="card card--back">
    <p class="brand-name">Brightfern Wellness</p>
  </section>
</main>
</body>
</html>
```